We need a new business card that reflects who we are. Professional, classy, modern, and service ori

We need a business card design for a window coverings design company in Kansas City called Bright Lane Interiors. We offer professional, modern, and high quality window covering products. We are looking to portray an image of a big, national franchise. We are a 5 location (with showrooms) business with 10 professional designers and 4 professional installers. These cards will be used with Thank you cards, given to realtors, and asked for referrals with.

Target Market(s)

Kansas City

Industry/Entity Type

Business

Contact Information for Business Card

We would like our card to look clean and simple on the front, featuring our logo and Marlow Fenwick's. Our designers' phone numbers and emails should be displayed as well as their title.

Font styles to use
Sans Serif

Colors

Designer to choose colors to be used in the design.

Requirements
Must have
• Front - Logos, name, phone number, email address
• Back - Showroom locations, social media? Appt date/time?
Nice to have
• I would like a clean and modern look (not contemporary. I like a white background, but I am open to ideas. Looking for a "National chain" look for a small business.
Should not have
• Too much busyness.

```html
<!DOCTYPE html>
<html lang="en">
<head>
<meta charset="utf-8">
<title>Bright Lane Interiors – Business Card</title>
<link rel="stylesheet" href="https://fonts.googleapis.com/css2?family=Roboto:wght@400;500;700&family=Roboto+Condensed:wght@700&display=swap">
<style>
  :root {
    --backdrop: #2b2b2b;
    --card: #f3f3f3;
    --brand-red: #c9434a;
    --brand-grey: #8d8f92;
    --ink: #1c1c1c;
    --text: #4a4a4a;
    --muted: #5e5e5e;
  }
  * { margin: 0; padding: 0; box-sizing: border-box; }
  html, body { width: 1200px; height: 960px; overflow: hidden; }
  body {
    background: var(--backdrop);
    font-family: "Roboto", Arial, sans-serif;
    position: relative;
  }
  .card {
    position: absolute;
    width: 600px;
    height: 342px;
    background: var(--card);
    overflow: hidden;
  }
  .card--front { left: 314px; top: 113px; }
  .card--back  { left: 311px; top: 472px; height: 343px; }

  /* Front */
  .name-marker {
    position: absolute; left: 0; top: 93px;
    width: 36px; height: 40px; background: var(--brand-red);
  }
  .holder { position: absolute; left: 44px; top: 91px; }
  .holder__name {
    font-family: "Roboto Condensed", "Arial Narrow", sans-serif;
    font-weight: 700; font-size: 23px; color: var(--brand-red);
    letter-spacing: 0.2px; line-height: 26px;
  }
  .holder__title {
    font-weight: 700; font-size: 14px; color: var(--ink);
    line-height: 18px; margin-top: 1px;
  }
  .contact { position: absolute; left: 41px; top: 236px; list-style: none; }
  .contact__item {
    display: flex; align-items: center; gap: 8px;
    font-size: 15px; color: var(--text); height: 19.5px;
  }
  .contact__icon { width: 14px; height: 14px; flex: none; }

  .brand { position: absolute; text-align: center; }
  .brand__name {
    display: flex; align-items: center; justify-content: center; gap: 7px;
    font-size: 21px; font-weight: 400; color: var(--ink); white-space: nowrap;
  }
  .brand__mark { width: 14px; height: 14px; background: var(--brand-red); flex: none; }
  .brand__tagline {
    font-size: 11.5px; color: var(--ink); margin-top: 6px; white-space: nowrap;
  }
  .card--front .brand { left: 318px; top: 244px; width: 242px; }
  .card--back .brand  { left: 50px; top: 120px; width: 224px; }

  .edge-band {
    position: absolute; left: 0; bottom: 0; width: 100%; height: 10px;
    background: var(--brand-grey);
  }
  .edge-band__accent {
    position: absolute; left: 402px; top: 0; width: 90px; height: 100%;
    background: var(--brand-red);
  }

  /* Back */
  .showrooms {
    position: absolute; right: 53px; top: 43px; text-align: right;
    list-style: none;
  }
  .showrooms__heading {
    font-weight: 700; font-size: 14px; color: var(--brand-red);
    line-height: 18px; letter-spacing: 0.2px;
  }
  .showrooms__item {
    font-weight: 400; font-size: 14.5px; color: var(--muted);
    line-height: 18px; letter-spacing: 0.3px;
  }
  .partner {
    position: absolute; right: 53px; top: 156px;
    display: flex; align-items: center; gap: 4px;
    font-size: 13px; font-weight: 500; color: var(--muted);
  }
  .partner__dot { width: 12px; height: 12px; border-radius: 50%; background: var(--brand-grey); }
  .social { position: absolute; right: 53px; top: 185px; display: flex; gap: 3px; }
  .social__dot { width: 17px; height: 17px; border-radius: 50%; background: var(--brand-red); }

  .appointment { position: absolute; left: 52px; color: var(--brand-red); font-size: 16px; }
  .appointment--name { top: 236px; width: 496px; }
  .appointment--when { top: 277px; width: 500px; }
  .appointment__row { display: flex; align-items: baseline; white-space: nowrap; }
  .appointment__fill {
    flex: 1; border-bottom: 1px dotted #777; margin: 0 4px; height: 1px;
    transform: translateY(-4px);
  }
  .appointment__fill--date { flex: 0 0 214px; margin: 0 2px 0 4px; }
  .appointment__fill--time { flex: 0 0 134px; }
  .appointment__unit { font-size: 12px; margin-left: 2px; }
</style>
</head>
<body>

  <section class="card card--front" aria-label="Business card front">
    <div class="name-marker"></div>
    <div class="holder">
      <p class="holder__name">EVAN CLARKE</p>
      <p class="holder__title">DESIGNER</p>
    </div>

    <ul class="contact">
      <li class="contact__item">
        <svg class="contact__icon" viewBox="0 0 16 16" aria-hidden="true">
          <path fill="#c9434a" d="M3.6 1.2l2.3 2.4-1.3 2.1c.9 2 2.6 3.7 4.6 4.6l2.1-1.3 2.4 2.3-1.2 2.4C7.1 13.5 2.5 8.9 1.3 3.4z"/>
        </svg>
        <span>913.555.0148</span>
      </li>
      <li class="contact__item">
        <svg class="contact__icon" viewBox="0 0 16 16" aria-hidden="true">
          <rect x="1" y="3.5" width="14" height="9.5" fill="#c9434a"/>
          <path d="M1.5 4.2L8 9l6.5-4.8" fill="none" stroke="#f3f3f3" stroke-width="1.2"/>
        </svg>
        <span>info@brightlaneinteriors.com</span>
      </li>
      <li class="contact__item">
        <svg class="contact__icon" viewBox="0 0 16 16" aria-hidden="true">
          <circle cx="8" cy="8" r="6.8" fill="#c9434a"/>
          <path d="M4 5.5c1.5.3 2.6-.6 3.8.6.8.8-.3 2 .7 2.7 1 .7 2.4.2 2.5 1.9M9.5 2.6c.3 1-.7 1.5.3 2.2" fill="none" stroke="#f3f3f3" stroke-width="1.2"/>
        </svg>
        <span>brightlaneinteriors.com</span>
      </li>
    </ul>

    <div class="brand">
      <p class="brand__name"><span class="brand__mark"></span>Bright Lane Interiors</p>
      <p class="brand__tagline">Blinds, Shades, Shutters, Draperies &amp; Decor</p>
    </div>

    <div class="edge-band"><div class="edge-band__accent"></div></div>
  </section>

  <section class="card card--back" aria-label="Business card back">
    <div class="brand">
      <p class="brand__name"><span class="brand__mark"></span>Bright Lane Interiors</p>
      <p class="brand__tagline">Blinds, Shades, Shutters, Draperies &amp; Decor</p>
    </div>

    <ul class="showrooms">
      <li class="showrooms__heading">SHOWROOM LOCATIONS</li>
      <li class="showrooms__item">BRIARWOOD</li>
      <li class="showrooms__item">LAKEVIEW PARK</li>
      <li class="showrooms__item">ELM CROSSING</li>
      <li class="showrooms__item">NORTHFIELD</li>
      <li class="showrooms__item">WESTBROOK</li>
    </ul>

    <p class="partner"><span class="partner__dot"></span>Marlow Fenwick</p>

    <div class="social" aria-label="Social media">
      <span class="social__dot"></span>
      <span class="social__dot"></span>
      <span class="social__dot"></span>
      <span class="social__dot"></span>
    </div>

    <div class="appointment appointment--name appointment__row">
      <span>Name :</span><span class="appointment__fill"></span>
    </div>
    <div class="appointment appointment--when appointment__row">
      <span>Date :</span><span class="appointment__fill appointment__fill--date"></span>
      <span>Time :</span><span class="appointment__fill appointment__fill--time"></span>
      <span class="appointment__unit">AM/PM</span>
    </div>
  </section>

</body>
</html>
```